The Brandwell Firm

We need a new design for our letterhead and envelopes. We are a personal injury and criminal defense firm so we need something modern and clean, but more on the professional/traditional side. Our new logo has two colors and is attached to the file so we need something that works well with those colors/matches the design. The following information needs to be on the letterhead:
Phone: (555) 214-3370
Fax: (555) 214-5186
Toll-Free: (888) 431-2059
Post Office Box 4721
Millbrook, SC 29555-4721
HarmClaimCounsel.example
PalmettoTrialAdvocates.example

Target Market(s)

Clients, government agencies, other law firms

Industry/Entity Type

Legal

Font styles to use
Sans Serif
Other font styles liked:
• Arial

Colors

Designer to choose colors to be used in the design.

Requirements
Must have
• Must look professional and clean, modern
Nice to have
• I would like to see a design that works with the logo but does not distract from the content that will be printed on it
Should not have
• Too many colors or crazy designs.

```html
<!DOCTYPE html>
<html lang="en">
<head>
<meta charset="utf-8">
<title>The Brandwell Firm — Stationery</title>
<link rel="stylesheet" href="https://fonts.googleapis.com/css2?family=Open+Sans:wght@400;600&display=swap">
<style>
  :root {
    --backdrop: #5c5c5c;
    --paper: #ffffff;
    --navy: #2e3192;
    --red: #c8313a;
    --ink: #3a3a3a;
    --fold: #d9d9d9;
  }
  * { margin: 0; padding: 0; box-sizing: border-box; }
  html, body { width: 1200px; height: 904px; overflow: hidden; }
  body {
    background: var(--backdrop);
    font-family: "Open Sans", Arial, sans-serif;
    color: var(--ink);
    position: relative;
  }
  .sheet {
    position: absolute;
    background: var(--paper);
    box-shadow: 0 2px 6px rgba(0,0,0,.25);
  }
  .letterhead { left: 41px; top: 108px; width: 511px; height: 722px; }
  .envelope-front { left: 584px; top: 253px; width: 528px; height: 262px; }
  .envelope-back { left: 584px; top: 555px; width: 528px; height: 263px; overflow: hidden; }

  .firm-name {
    display: flex; align-items: center; gap: 6px;
    color: var(--navy);
    font-weight: 600;
    white-space: nowrap;
    position: absolute;
  }
  .firm-name .dot {
    width: 8px; height: 8px; border-radius: 50%;
    background: var(--red); flex: none;
  }
  .letterhead .firm-name { left: 42px; top: 56px; font-size: 15px; }
  .envelope-front .firm-name { left: 30px; top: 60px; font-size: 15px; }
  .envelope-back .firm-name {
    left: 50%; top: 30px; transform: translateX(-50%); font-size: 11px;
  }
  .envelope-back .firm-name .dot { width: 6px; height: 6px; }

  .contact {
    position: absolute; left: 358px; top: 42px;
    font-size: 7.6px; line-height: 10.5px; list-style: none;
  }
  .contact li { display: flex; align-items: center; gap: 5px; }
  .contact li.plain { padding-left: 0; }
  .contact svg { width: 7px; height: 7px; flex: none; }

  .return-address {
    position: absolute; left: 52px; top: 96px; width: 120px;
    text-align: center; font-size: 7.6px; line-height: 10.5px;
  }
  .flap { position: absolute; left: 0; top: 0; width: 528px; height: 90px; }
</style>
</head>
<body>

<section class="sheet letterhead" aria-label="Letterhead">
  <div class="firm-name"><span class="dot"></span>The Brandwell Firm</div>
  <ul class="contact">
    <li>Post Office Box 4721</li>
    <li>Millbrook, SC 29555-4721</li>
    <li style="margin-top:3px">
      <svg viewBox="0 0 10 10" aria-hidden="true"><path fill="var(--navy)" d="M1 3 Q5 0 9 3 L8 5 L6.5 4 L6.5 3.2 Q5 2.7 3.5 3.2 L3.5 4 L2 5 Z M3 5.5 H7 L8 9 H2 Z"/></svg>
      (555) 214-3370</li>
    <li>
      <svg viewBox="0 0 10 10" aria-hidden="true"><path fill="var(--navy)" d="M3 1 H7 V4 H3 Z M1 4.5 H9 V9 H1 Z"/></svg>
      (555) 214-5186</li>
    <li>
      <svg viewBox="0 0 10 10" aria-hidden="true"><circle cx="5" cy="5" r="4.2" fill="none" stroke="var(--navy)" stroke-width="1.2"/><path fill="var(--navy)" d="M3.3 2.8 L4.5 2.8 L4.8 4 L4.1 4.5 Q4.7 5.6 5.6 6 L6.1 5.3 L7.2 5.6 L7.2 6.8 Q4 7 3.3 2.8 Z"/></svg>
      (888) 431-2059</li>
    <li>
      <svg viewBox="0 0 10 10" aria-hidden="true"><g fill="none" stroke="var(--navy)" stroke-width="1"><circle cx="5" cy="5" r="4.2"/><ellipse cx="5" cy="5" rx="1.8" ry="4.2"/><path d="M1 5 H9"/></g></svg>
      HarmClaimCounsel.example</li>
    <li>
      <svg viewBox="0 0 10 10" aria-hidden="true"><g fill="none" stroke="var(--navy)" stroke-width="1"><circle cx="5" cy="5" r="4.2"/><ellipse cx="5" cy="5" rx="1.8" ry="4.2"/><path d="M1 5 H9"/></g></svg>
      PalmettoTrialAdvocates.example</li>
  </ul>
</section>

<section class="sheet envelope-front" aria-label="Envelope front">
  <div class="firm-name"><span class="dot"></span>The Brandwell Firm</div>
  <p class="return-address">Post Office Box 4721<br>Millbrook, SC 29555-4721</p>
</section>

<section class="sheet envelope-back" aria-label="Envelope back">
  <svg class="flap" viewBox="0 0 528 90" aria-hidden="true">
    <path d="M0 4 Q4 30 40 44 L264 78 L488 44 Q524 30 528 4" fill="none" stroke="rgba(0,0,0,.08)" stroke-width="6"/>
    <path d="M0 4 Q4 30 40 44 L264 78 L488 44 Q524 30 528 4" fill="none" stroke="var(--fold)" stroke-width="1"/>
  </svg>
  <div class="firm-name"><span class="dot"></span>The Brandwell Firm</div>
</section>

</body>
</html>
```